Brell Stone Company Business Cards

Front and Back Business Card - logo and text setup - cool design. I need workable photoshop or illustrator files so I can setup each employee card with design that is created
Updates

Hi everyone, thank you for the great entries. Please no more white and blue cards - there are so many already - black and silver only now please. thanks!

Target Market(s)

Construction Industry - Facility Managers

Industry/Entity Type

Construction

Contact Information for Business Card

I really like contemporary simplistic looks - clean neat....not opposed to seeing some black backrounds

Requirements
Must have
• Logo/website address with design on front only - www.brellstone-example.com (logo attached)
• Back:
• Name/Title/Company Address/Phone/email address
Nice to have
• Cool design
Should not have
• Nothing gimmicky like Fire or Water - since we are a Fire Protection company - it has all been done

```html
<!DOCTYPE html>
<html lang="en">
<head>
<meta charset="utf-8">
<title>Brell Stone Company Business Cards</title>
<link rel="stylesheet" href="https://fonts.googleapis.com/css2?family=Lato:wght@400;700;900&display=swap">
<style>
  :root {
    --backdrop: #141414;
    --card: #262626;
    --card-edge: #303030;
    --silver: #b9b9b9;
    --navy: #2e3f7c;
    --red: #e8402f;
    --white: #f2f2f2;
  }
  * { margin: 0; padding: 0; box-sizing: border-box; }
  html, body {
    width: 1200px; height: 912px; overflow: hidden;
    background: var(--backdrop);
    font-family: "Lato", sans-serif;
    color: var(--white);
  }
  .card {
    position: absolute; left: 250px;
    width: 700px; height: 400px;
    background: var(--card);
    border: 1px solid var(--card-edge);
    overflow: hidden;
  }
  .card--front { top: 40px; }
  .card--back { top: 472px; }

  /* Front */
  .front-brand {
    position: absolute; left: 0; right: 0; top: 120px;
    display: flex; align-items: center; justify-content: center; gap: 14px;
  }
  .front-brand__mark { width: 22px; height: 22px; background: var(--silver); }
  .front-brand__name {
    font-weight: 900; font-size: 76px; letter-spacing: -1px;
    color: var(--silver); line-height: 1;
  }
  .front-web {
    position: absolute; left: 0; right: 0; top: 290px;
    text-align: center; font-size: 19px; letter-spacing: 0.5px;
  }

  /* Back */
  .back-brand {
    position: absolute; left: 50px; top: 150px;
    display: flex; align-items: center; gap: 10px;
  }
  .back-brand__mark { width: 16px; height: 16px; background: var(--navy); }
  .back-brand__name {
    font-weight: 900; font-size: 48px; letter-spacing: -1px;
    color: var(--navy); line-height: 1;
  }
  .divider {
    position: absolute; left: 365px; top: 95px;
    width: 1px; height: 175px; background: var(--red);
  }
  .person { position: absolute; left: 390px; top: 90px; }
  .person__name { font-size: 26px; font-weight: 700; color: var(--red); line-height: 1.15; }
  .person__title { font-size: 17px; margin-top: 2px; }
  .contacts { list-style: none; margin-top: 14px; }
  .contacts li {
    display: flex; align-items: center; gap: 10px;
    font-size: 16px; line-height: 1.55;
  }
  .contacts svg { width: 14px; height: 14px; flex: none; }
  .address {
    position: absolute; right: 40px; bottom: 40px;
    font-size: 19px; letter-spacing: 0.2px;
  }
  .band {
    position: absolute; left: 0; right: 0; bottom: 0;
    height: 10px; background: var(--red);
  }
</style>
</head>
<body>

<section class="card card--front" aria-label="Card front">
  <div class="front-brand">
    <span class="front-brand__mark"></span>
    <span class="front-brand__name">brellstone</span>
  </div>
  <p class="front-web">www.brellstone-example.com</p>
</section>

<section class="card card--back" aria-label="Card back">
  <div class="back-brand">
    <span class="back-brand__mark"></span>
    <span class="back-brand__name">brellstone</span>
  </div>
  <div class="divider"></div>
  <div class="person">
    <p class="person__name">Dana Merrow Lyle</p>
    <p class="person__title">President</p>
    <ul class="contacts">
      <li>
        <svg viewBox="0 0 16 16" aria-hidden="true"><path fill="var(--red)" d="M3.5 1l3 3-1.8 1.8a9 9 0 0 0 5.5 5.5L12 9.5l3 3-2 2.5C7 15 1 9 1 3z"/></svg>
        (555) 014-2870
      </li>
      <li>
        <svg viewBox="0 0 16 16" aria-hidden="true"><rect x="1" y="3" width="14" height="10" fill="var(--red)"/><path d="M1.5 3.5L8 9l6.5-5.5" fill="none" stroke="var(--card)" stroke-width="1.4"/></svg>
        info@brellstone-example.com
      </li>
      <li>
        <svg viewBox="0 0 16 16" aria-hidden="true"><circle cx="8" cy="8" r="6.5" fill="none" stroke="var(--red)" stroke-width="1.5"/><ellipse cx="8" cy="8" rx="2.8" ry="6.5" fill="none" stroke="var(--red)" stroke-width="1.2"/><path d="M1.5 8h13M2.5 5h11M2.5 11h11" stroke="var(--red)" stroke-width="1.1"/></svg>
        www.brellstone-example.com
      </li>
    </ul>
  </div>
  <p class="address">48 Harbor Works Road, Millbrook, NY 10990</p>
  <div class="band"></div>
</section>

</body>
</html>
```